Walk Beside The River

Business Card design

Target Market(s)

People who require support in the commnity

Industry/Entity Type

Mental Health Support

Contact Information for Business Card

Mental Health Support Rosalind Tavener walkbesidetheriver@mailcove.com.au 0481 637 092 PO Box 926 Wattle Cove QLD 4571

Colors
6B429C
8869AF
B7A5CE
E3DAEB
F3F0F8

Requirements
Must have
• Logo & details listed above
Should not have
• No red or orange

```html
<!DOCTYPE html>
<html lang="en">
<head>
<meta charset="utf-8">
<title>Walk Beside The River – Business Card</title>
<link href="https://fonts.googleapis.com/css2?family=Lato:wght@400;700;900&display=swap" rel="stylesheet">
<style>
  :root {
    --page-bg: #ebe7ee;
    --violet-deep: #3b1d63;
    --violet-badge: #432670;
    --violet: #6B429C;
    --violet-soft: #8869AF;
    --lilac: #B7A5CE;
    --mist: #E3DAEB;
    --pearl: #F3F0F8;
    --ink-light: #efe8ef;
  }
  * { box-sizing: border-box; margin: 0; padding: 0; }
  html, body {
    width: 1200px;
    height: 734px;
    overflow: hidden;
    background: var(--page-bg);
    font-family: "Lato", sans-serif;
  }
  .card {
    position: absolute;
    left: 60px;
    top: 57px;
    width: 1080px;
    height: 620px;
    border-radius: 26px;
    overflow: hidden;
    background:
      radial-gradient(ellipse 260px 420px at 240px 430px, rgba(136,105,175,0.85), rgba(136,105,175,0) 70%),
      radial-gradient(ellipse 140px 200px at 20px 140px, rgba(136,105,175,0.7), rgba(136,105,175,0) 75%),
      linear-gradient(90deg, #5d3f86 0%, var(--violet-soft) 18%, #6a4a98 32%, var(--violet-deep) 52%, #3f2168 70%, var(--violet) 100%);
    box-shadow: 0 12px 30px rgba(60, 40, 80, 0.18);
  }
  .card__panel {
    position: absolute;
    inset: 0;
  }
  .holder {
    position: absolute;
    left: 57px;
    top: 174px;
    color: var(--ink-light);
  }
  .holder__name {
    font-weight: 900;
    font-size: 46px;
    letter-spacing: -0.5px;
    line-height: 1;
    text-transform: uppercase;
  }
  .holder__role {
    margin-top: 6px;
    font-size: 28px;
    font-weight: 400;
    letter-spacing: 0.5px;
  }
  .contact {
    position: absolute;
    left: 57px;
    color: var(--ink-light);
    display: flex;
    align-items: flex-start;
    gap: 14px;
  }
  .contact svg { flex: none; fill: var(--ink-light); }
  .contact--address { top: 283px; font-size: 25px; line-height: 38px; letter-spacing: 0.4px; }
  .contact--address svg { margin-top: 6px; }
  .contact--phone { top: 366px; font-size: 33px; font-weight: 700; letter-spacing: 0.5px; align-items: center; }
  .contact--email { top: 413px; font-size: 24px; letter-spacing: 0.3px; align-items: center; }
  .brand {
    position: absolute;
    left: 660px;
    top: 150px;
    width: 336px;
    height: 336px;
    border-radius: 50%;
    background: var(--violet-badge);
    display: flex;
    align-items: center;
    justify-content: center;
  }
  .brand__name {
    font-weight: 700;
    font-size: 34px;
    line-height: 1.25;
    text-align: center;
    letter-spacing: 1px;
    color: var(--mist);
  }
</style>
</head>
<body>
  <div class="card">
    <svg class="card__panel" width="1080" height="620" viewBox="0 0 1080 620" aria-hidden="true">
      <defs>
        <linearGradient id="panelFill" x1="0" y1="0" x2="0" y2="1">
          <stop offset="0" stop-color="#d8d2d7"/>
          <stop offset="1" stop-color="#e6e2e9"/>
        </linearGradient>
      </defs>
      <circle cx="853" cy="310" r="313" fill="url(#panelFill)"/>
      <rect x="853" y="0" width="227" height="620" fill="url(#panelFill)"/>
    </svg>

    <div class="holder">
      <h1 class="holder__name">Rosalind Tavener</h1>
      <p class="holder__role">Mental Health Support</p>
    </div>

    <div class="contact contact--address">
      <svg width="22" height="30" viewBox="0 0 22 30" aria-hidden="true">
        <path d="M11 0C4.9 0 0 4.8 0 10.8 0 18.5 11 30 11 30s11-11.5 11-19.2C22 4.8 17.1 0 11 0zm0 15a4.3 4.3 0 1 1 0-8.6 4.3 4.3 0 0 1 0 8.6z"/>
      </svg>
      <p>PO Box 926<br>Wattle Cove QLD 4571</p>
    </div>

    <div class="contact contact--phone">
      <svg width="24" height="24" viewBox="0 0 24 24" aria-hidden="true">
        <path d="M6.6 10.8a15.1 15.1 0 0 0 6.6 6.6l2.2-2.2c.3-.3.7-.4 1-.2 1.1.4 2.3.6 3.6.6.6 0 1 .4 1 1V20c0 .6-.4 1-1 1A17 17 0 0 1 3 4c0-.6.4-1 1-1h3.5c.6 0 1 .4 1 1 0 1.3.2 2.5.6 3.6.1.3 0 .7-.2 1l-2.3 2.2z"/>
      </svg>
      <p>0481 637 092</p>
    </div>

    <div class="contact contact--email">
      <svg width="24" height="18" viewBox="0 0 24 18" aria-hidden="true">
        <path d="M0 0h24v18H0z M2 2.5v13h20v-13l-10 7z" fill-rule="evenodd"/>
      </svg>
      <p>walkbesidetheriver@mailcove.com.au</p>
    </div>

    <div class="brand">
      <p class="brand__name">Walk Beside<br>The River</p>
    </div>
  </div>
</body>
</html>
```